Weightloss company needs Business Card

We want a business card that is clean and professional, yet portrays that we are a friendly, innovative, and versatile program designed to fit the needs of our clients.
I would like there to be 2 sides, one side having an appointment card, and the other side containing the logo and business information. There can be decorations on both sides. The logo is attached.

Target Market(s)

Men and women 40-60

Industry/Entity Type

Business

Contact Information for Business Card

Font styles to use
Sans Serif

Requirements
Must have
• The logo, space for business information
Nice to have
• The colors in the logo
Should not have
• No pictures of people or food

```html
<!DOCTYPE html>
<html lang="en">
<head>
<meta charset="utf-8">
<title>Rise Path Wellness – Business Card</title>
<link rel="stylesheet" href="https://fonts.googleapis.com/css2?family=Open+Sans:ital,wght@0,400;0,600;1,400&display=swap">
<style>
  :root {
    --brand-red: #d9002b;
    --card-white: #f4f4f5;
    --ink-grey: #55565a;
    --page-bg: #8f8f90;
    --dot-grey: #6a6a6a;
  }
  * { box-sizing: border-box; margin: 0; padding: 0; }
  html, body { width: 1105px; height: 1200px; overflow: hidden; }
  body {
    background: var(--page-bg);
    font-family: "Open Sans", Arial, sans-serif;
    position: relative;
  }
  .card {
    position: absolute;
    left: 182px;
    width: 746px;
    height: 426px;
    background: var(--card-white);
    overflow: hidden;
  }
  .card--front { top: 119px; }
  .card--back { top: 635px; }

  /* Front */
  .brand-name {
    position: absolute;
    left: 52px; top: 72px;
    width: 236px;
    color: var(--brand-red);
    font-weight: 600;
    font-size: 29px;
    line-height: 1.08;
    display: flex; align-items: center; gap: 12px;
    z-index: 2;
  }
  .brand-dot {
    width: 16px; height: 16px; border-radius: 50%;
    background: var(--brand-red); flex: none;
  }
  .name-band {
    position: absolute;
    left: 300px; top: 47px; right: 0; height: 116px;
    background: var(--brand-red);
  }
  .person-name {
    position: absolute; left: 147px; top: 26px;
    color: #fff; font-weight: 600; font-size: 27px; letter-spacing: 0.2px;
  }
  .person-title {
    position: absolute; left: 147px; top: 64px;
    color: #fff; font-size: 19px;
  }
  .contact-list {
    position: absolute; left: 449px; top: 245px;
    list-style: none;
  }
  .contact-list li {
    display: flex; align-items: center; gap: 12px;
    height: 28.5px;
    color: var(--ink-grey); font-size: 19px;
  }
  .contact-list svg { width: 18px; height: 18px; fill: var(--brand-red); flex: none; }
  .address {
    position: absolute; left: 52px; top: 333px;
    color: var(--ink-grey); font-size: 19px; line-height: 27px;
    font-style: normal;
  }

  /* Back */
  .appointment-title {
    position: absolute; top: 36px; left: 0; right: 0;
    text-align: center; color: var(--brand-red);
    font-weight: 600; font-size: 28px;
  }
  .form-row {
    position: absolute; left: 41px; right: 56px;
    display: flex; align-items: baseline;
    color: var(--brand-red); font-size: 20px;
  }
  .fill-line {
    flex: 1; margin-left: 8px;
    border-bottom: 2px dotted var(--dot-grey);
    transform: translateY(-4px);
  }
  .row-name { top: 104px; }
  .row-datetime { top: 156px; left: 38px; }
  .row-datetime .fill-line--date { flex: 0 0 282px; margin-right: 24px; }
  .ampm { font-size: 15px; margin-left: 6px; }
  .row-days {
    top: 217px; left: 44px; right: 58px;
    justify-content: space-between; font-size: 19px;
  }
  .day { display: flex; align-items: center; gap: 6px; }
  .tick-box {
    width: 22px; height: 19px;
    border: 1.5px solid var(--ink-grey); background: #fff;
  }
  .row-note { top: 262px; }
  .row-extra { top: 306px; }
  .row-extra .fill-line { margin-left: 0; }
  .cancel-note {
    position: absolute; top: 359px; left: 0; right: 0;
    text-align: center; font-style: italic;
    font-size: 15px; line-height: 21px; color: var(--ink-grey);
  }
</style>
</head>
<body>

<section class="card card--front" aria-label="Business card front">
  <div class="name-band">
    <div class="person-name">DANIEL HARPER</div>
    <div class="person-title">CEO/FOUNDER</div>
  </div>
  <div class="brand-name"><span class="brand-dot"></span><span>Rise Path<br>Wellness</span></div>
  <ul class="contact-list">
    <li><svg viewBox="0 0 24 24" aria-hidden="true"><path d="M6.6 10.8a15.1 15.1 0 0 0 6.6 6.6l2.2-2.2a1 1 0 0 1 1-.25 11.4 11.4 0 0 0 3.6.57 1 1 0 0 1 1 1V20a1 1 0 0 1-1 1A17 17 0 0 1 3 4a1 1 0 0 1 1-1h3.5a1 1 0 0 1 1 1c0 1.250.2 2.450.57 3.57a1 1 0 0 1-.25 1z"/></svg>555 201 4410</li>
    <li><svg viewBox="0 0 24 24" aria-hidden="true"><path d="M7 1h10a2 2 0 0 1 2 2v18a2 2 0 0 1-2 2H7a2 2 0 0 1-2-2V3a2 2 0 0 1 2-2zm0 3v14h10V4zm5 15.5a1.2 1.2 0 1 0 0 2.4 1.2 1.2 0 0 0 0-2.4z"/></svg>555 318 2276</li>
    <li><svg viewBox="0 0 24 24" aria-hidden="true"><path d="M6 2h9l3 3v4H6zM3 10h18a2 2 0 0 1 2 2v7h-4v3H5v-3H1v-7a2 2 0 0 1 2-2zm4 6v4h10v-4z"/></svg>555 467 9082</li>
    <li><svg viewBox="0 0 24 24" aria-hidden="true"><path d="M2 5h20v14H2zm2 2v.5l8 5.5 8-5.5V7zm0 3v7h16v-7l-8 5.5z"/></svg>hello@risepath.com</li>
    <li><svg viewBox="0 0 24 24" aria-hidden="true"><path d="M12 2a10 10 0 1 0 0 20 10 10 0 0 0 0-20zm-1 17.9A8 8 0 0 1 4.2 10.5L9 15.3v1a2 2 0 0 0 2 2zm6.9-2.5A2 2 0 0 0 16 16h-1v-3a1 1 0 0 0-1-1H8v-2h2a1 1 0 0 0 1-1V7h2a2 2 0 0 0 2-2v-.4a8 8 0 0 1 2.9 12.8z"/></svg>www.risepath.com</li>
  </ul>
  <address class="address">1420 Birchwood Avenue<br>Fairview, Oregon 97024</address>
</section>

<section class="card card--back" aria-label="Appointment card back">
  <h2 class="appointment-title">Next Appointment</h2>
  <div class="form-row row-name">Name :<span class="fill-line"></span></div>
  <div class="form-row row-datetime">Date :<span class="fill-line fill-line--date"></span>Time :<span class="fill-line"></span><span class="ampm">AM/PM</span></div>
  <div class="form-row row-days">
    <span class="day">Sun <span class="tick-box"></span></span>
    <span class="day">Mon <span class="tick-box"></span></span>
    <span class="day">Tue <span class="tick-box"></span></span>
    <span class="day">Wed <span class="tick-box"></span></span>
    <span class="day">Thu<span class="tick-box"></span></span>
    <span class="day">Fri<span class="tick-box"></span></span>
    <span class="day">Sat <span class="tick-box"></span></span>
  </div>
  <div class="form-row row-note">Note :<span class="fill-line"></span></div>
  <div class="form-row row-extra"><span class="fill-line"></span></div>
  <p class="cancel-note">Please give me 24 hours notice if you are unable to keep your appointment or<br>a cancellation fee may be charged.</p>
</section>

</body>
</html>
```